Corvane Paintless Dent Removal

Our company works on vehicles removing dents using a highly skilled trade which the metal is massaged out with special tools without disturbing the original paint, hence paintless dent removal. Besides keeping the paint and metal original its also very environmentally friendly since no paint or toxic fillers are used. Also we we are one of the most experienced companies in the business with 25 years

Target Market(s)

Retail Automobile consumers, Auto Dealerships and Auto Body Shops

Industry/Entity Type

Auto Repair

Contact Information for Business Card

Dale Hollister
PO Box 518 Brookmere, NY 11962
631-555-0148
corvanepdr@mailbox-example.com
website corvanepdr.example
youtube corvane paintless dent removal
25 years of experience removing Dents, Dings and Hail Damage

Font styles to use
Serif
Sans Serif

Colors

Designer to choose colors to be used in the design.

Requirements
Must have
• I do like things that are simple but classy and somewhat bold, also I like my logo so that should be somewhat important

```html
<!DOCTYPE html>
<html lang="en">
<head>
<meta charset="utf-8">
<title>Corvane Paintless Dent Removal – Business Card</title>
<link rel="stylesheet" href="https://fonts.googleapis.com/css2?family=Roboto:wght@400;500;700;900&family=Roboto+Condensed:wght@400;700&display=swap">
<style>
  :root {
    --navy: #13294f;
    --green: #7cc242;
    --white: #ffffff;
    --paper: #f6f6f4;
    --ink: #2b2f3a;
    --gold: #d8a628;
    --gold-dark: #1b1a14;
    --stage: #e4e2dd;
  }
  * { box-sizing: border-box; margin: 0; padding: 0; }
  html, body { width: 1200px; height: 911px; overflow: hidden; }
  body {
    background: var(--stage);
    font-family: "Roboto", Arial, sans-serif;
    display: flex;
    align-items: center;
    justify-content: center;
    gap: 40px;
  }
  .card {
    position: relative;
    width: 540px;
    height: 309px;
    overflow: hidden;
    box-shadow: 0 6px 18px rgba(0,0,0,.18);
  }
  .card-front { background: var(--navy); }
  .card-front .frame { position: absolute; inset: 0; }
  .brand-name {
    position: absolute;
    left: 48px;
    top: 40px;
    color: var(--navy);
    font-family: "Roboto Condensed", Arial, sans-serif;
    font-weight: 700;
    line-height: 1.05;
  }
  .brand-name .word { display: block; font-size: 34px; letter-spacing: .5px; }
  .brand-name .tag { display: block; font-size: 15px; }
  .contact {
    position: absolute;
    left: 62px;
    bottom: 46px;
    color: var(--ink);
    font-size: 12.5px;
    line-height: 1.55;
  }
  .contact .person {
    font-family: "Roboto Condensed", Arial, sans-serif;
    font-weight: 700;
    font-size: 17px;
    color: var(--navy);
    text-transform: uppercase;
    margin-bottom: 4px;
    letter-spacing: .3px;
  }
  .contact li { list-style: none; display: flex; align-items: center; gap: 8px; }
  .contact svg { width: 11px; height: 11px; flex: none; fill: var(--navy); }

  .card-back { background: var(--navy); color: var(--white); }
  .back-brand {
    position: absolute;
    left: 40px;
    top: 46px;
    font-family: "Roboto Condensed", Arial, sans-serif;
    font-weight: 700;
    line-height: 1;
  }
  .back-brand .word { display: block; font-size: 52px; letter-spacing: .5px; }
  .back-brand .tag { display: block; font-size: 19px; margin-top: 4px; }
  .back-brand .site {
    display: block;
    font-family: "Roboto", Arial, sans-serif;
    font-weight: 400;
    font-size: 14px;
    letter-spacing: 2.6px;
    margin-top: 8px;
  }
  .seal {
    position: absolute;
    right: 26px;
    top: 22px;
    width: 64px;
    height: 64px;
    border-radius: 50%;
    background: var(--gold-dark);
    border: 3px solid var(--gold);
    color: var(--gold);
    display: flex;
    flex-direction: column;
    align-items: center;
    justify-content: center;
    font-family: "Roboto Condensed", Arial, sans-serif;
    font-weight: 700;
    line-height: .95;
  }
  .seal .num { font-size: 24px; }
  .seal .unit { font-size: 9px; letter-spacing: 1px; }
</style>
</head>
<body>

  <section class="card card-front" aria-label="Business card front">
    <svg class="frame" width="540" height="309" viewBox="0 0 540 309" aria-hidden="true">
      <ellipse cx="270" cy="154" rx="330" ry="176" transform="rotate(-8 270 154)" fill="none" stroke="var(--green)" stroke-width="8"/>
      <ellipse cx="266" cy="158" rx="322" ry="170" transform="rotate(-8 266 158)" fill="var(--paper)"/>
    </svg>

    <div class="brand-name">
      <span class="word">CORVANE</span>
      <span class="tag">Paintless Dent Removal</span>
    </div>

    <div class="contact">
      <p class="person">Dale Hollister</p>
      <ul>
        <li><svg viewBox="0 0 24 24"><path d="M6.6 10.8a15 15 0 0 0 6.6 6.6l2.2-2.2a1 1 0 0 1 1-.25 11.4 11.4 0 0 0 3.6.57 1 1 0 0 1 1 1V20a1 1 0 0 1-1 1A17 17 0 0 1 3 4a1 1 0 0 1 1-1h3.5a1 1 0 0 1 1 1c0 1.25.2 2.45.57 3.57a1 1 0 0 1-.25 1z"/></svg>631-555-0148</li>
        <li><svg viewBox="0 0 24 24"><path d="M2 5h20v14H2zm2 2v.5l8 5 8-5V7l-8 5z"/></svg>corvanepdr@mailbox-example.com</li>
        <li><svg viewBox="0 0 24 24"><circle cx="12" cy="12" r="10"/></svg>corvanepdr.example</li>
        <li><svg viewBox="0 0 24 24"><rect x="2" y="2" width="20" height="20" rx="3"/></svg>corvane paintless dent removal</li>
        <li><svg viewBox="0 0 24 24"><path d="M12 2a7 7 0 0 0-7 7c0 5.2 7 13 7 13s7-7.8 7-13a7 7 0 0 0-7-7zm0 9.5A2.5 2.5 0 1 1 12 6.5a2.5 2.5 0 0 1 0 5z"/></svg>PO Box 518 Brookmere, NY 11962</li>
      </ul>
    </div>
  </section>

  <section class="card card-back" aria-label="Business card back">
    <div class="seal" aria-label="25 years of experience">
      <span class="num">25</span>
      <span class="unit">YEARS</span>
    </div>
    <div class="back-brand">
      <span class="word">CORVANE</span>
      <span class="tag">Paintless Dent Removal</span>
      <span class="site">corvanepdr.example</span>
    </div>
  </section>

</body>
</html>
```